Small Business Broker Business Card Design

A business card design for a small business brokerage, which is a financial service, not unlike real estate brokerage, but for small businesses such as laundromats, pizza shops, restaurants, cleaners etc. The designs should all be simple, more conservative in nature, using the colors and font of the logo. Again, think real estate Brokerage as a business context
Contact Information for Business Card
Name: Glen R. Harlow. Title: Small Business Advisor. Email: g.harlow@bayfieldcapitalworks.example. Mobile: (555) 274-3918. Office: (555) 806-2147. www.bayfieldcapitalworks.example

```html
<!DOCTYPE html>
<html lang="en">
<head>
<meta charset="utf-8">
<title>Bayfield Capital Works – Business Card</title>
<link href="https://fonts.googleapis.com/css2?family=Roboto+Condensed:wght@400;700&display=swap" rel="stylesheet">
<style>
  :root {
    --bg: #222222;
    --green: #8dc63f;
    --green-deep: #6fa52c;
    --navy: #163a6e;
    --ink: #1d1d1d;
    --white: #ffffff;
  }
  * { margin: 0; padding: 0; box-sizing: border-box; }
  html, body { width: 1200px; height: 780px; overflow: hidden; background: var(--bg); }
  body { font-family: "Roboto Condensed", Arial, sans-serif; position: relative; }

  .card {
    position: absolute;
    top: 235px;
    width: 540px;
    height: 309px;
    box-shadow: 0 12px 30px rgba(0,0,0,.55);
    overflow: hidden;
  }
  .card--front { left: 50px; background: var(--white); }
  .card--back { left: 610px; background: var(--green); }

  .front-swoosh { position: absolute; inset: 0; }

  .brand { position: absolute; left: 40px; top: 62px; width: 215px; }
  .brand__row { display: flex; align-items: center; gap: 7px; }
  .brand__mark { width: 14px; height: 14px; background: var(--navy); flex: none; }
  .brand__name { color: var(--navy); font-weight: 700; font-size: 13px; letter-spacing: .4px; text-transform: uppercase; white-space: nowrap; }
  .brand__tagline { margin-top: 4px; padding-left: 21px; color: var(--green); font-size: 7.5px; letter-spacing: .6px; text-transform: uppercase; white-space: nowrap; }

  .divider { position: absolute; left: 268px; top: 48px; width: 1.5px; height: 140px; background: var(--ink); }

  .contact { position: absolute; left: 290px; top: 60px; }
  .contact__name { color: var(--green); font-weight: 700; font-size: 28px; line-height: 1; }
  .contact__title { color: var(--ink); font-size: 14px; margin-top: 4px; margin-bottom: 14px; }
  .contact__list { list-style: none; }
  .contact__item { display: flex; align-items: center; gap: 8px; color: var(--ink); font-size: 13.5px; line-height: 21px; white-space: nowrap; }
  .contact__icon { width: 12px; height: 12px; flex: none; }

  .back-brand { position: absolute; inset: 0; display: flex; flex-direction: column; align-items: center; justify-content: center; gap: 10px; }
  .back-brand__row { display: flex; align-items: center; gap: 12px; }
  .back-brand__mark { width: 26px; height: 26px; background: var(--green-deep); }
  .back-brand__name { color: var(--green-deep); font-weight: 700; font-size: 26px; letter-spacing: 1px; text-transform: uppercase; white-space: nowrap; }
  .back-brand__tagline { color: var(--green-deep); font-size: 11px; letter-spacing: 1.5px; text-transform: uppercase; white-space: nowrap; }
</style>
</head>
<body>

<section class="card card--front">
  <svg class="front-swoosh" viewBox="0 0 540 309" width="540" height="309" aria-hidden="true">
    <path d="M0 110 C40 190 170 285 440 309 L0 309 Z" fill="var(--green)"/>
    <path d="M105 200 C190 262 300 296 440 309" fill="none" stroke="var(--white)" stroke-width="10"/>
    <path d="M105 200 C190 262 300 296 440 309" fill="none" stroke="var(--navy)" stroke-width="4"/>
  </svg>

  <div class="brand">
    <div class="brand__row">
      <span class="brand__mark"></span>
      <span class="brand__name">Bayfield Capital Works, Inc</span>
    </div>
    <p class="brand__tagline">Trusted guidance for every main street sale</p>
  </div>

  <div class="divider"></div>

  <div class="contact">
    <h1 class="contact__name">Glen R. Harlow</h1>
    <p class="contact__title">Small Business Advisor</p>
    <ul class="contact__list">
      <li class="contact__item">
        <svg class="contact__icon" viewBox="0 0 12 12" aria-hidden="true"><rect x="3" y="0.5" width="6" height="11" rx="1" fill="none" stroke="var(--navy)" stroke-width="1.2"/></svg>
        (555) 274-3918
      </li>
      <li class="contact__item">
        <svg class="contact__icon" viewBox="0 0 12 12" aria-hidden="true"><path d="M2.5 1 L4.5 1 L5.2 3.6 L4 4.6 C4.7 6 6 7.3 7.4 8 L8.4 6.8 L11 7.5 L11 9.5 C11 10.5 10 11 9 11 C4.5 10.5 1.5 7.5 1 3 C1 2 1.5 1 2.5 1 Z" fill="var(--green)"/></svg>
        (555) 806-2147
      </li>
      <li class="contact__item">
        <svg class="contact__icon" viewBox="0 0 12 12" aria-hidden="true"><circle cx="6" cy="6" r="5.3" fill="var(--navy)"/><path d="M0.8 6 H11.2 M6 0.7 C3.5 3 3.5 9 6 11.3 M6 0.7 C8.5 3 8.5 9 6 11.3" fill="none" stroke="var(--white)" stroke-width="0.8"/></svg>
        www.bayfieldcapitalworks.example
      </li>
      <li class="contact__item">
        <svg class="contact__icon" viewBox="0 0 12 12" aria-hidden="true"><rect x="0.5" y="2" width="11" height="8" fill="var(--green)"/><path d="M0.5 2 L6 6.5 L11.5 2" fill="none" stroke="var(--white)" stroke-width="1"/></svg>
        g.harlow@bayfieldcapitalworks.example
      </li>
    </ul>
  </div>
</section>

<section class="card card--back">
  <div class="back-brand">
    <div class="back-brand__row">
      <span class="back-brand__mark"></span>
      <span class="back-brand__name">Bayfield Capital Works, Inc</span>
    </div>
    <p class="back-brand__tagline">Trusted guidance for every main street sale</p>
  </div>
</section>

</body>
</html>
```